velmora - customer deliverable template

Scribo Template Design for Client Deliverables

We are looking for a professional and polished Scribo template for our client deliverables, including RFP responses, business proposals, technical proposals, and workshop reports. The template must be fully aligned with our corporate style and branding.

To kick things off, we'll start with our Insight Horizon Session deliverable document as the base for the new template. This is a very simple project with very limited effort.

Project Resources
All necessary documentation and assets can be found in the following Nimbus Vault folder:
https://files.nimbusvault.example/folders/7k3QpzRtaWmxYbLcVnHeDsFgJuKoPiA2?usp=share_link

The folder includes:
Assets: A folder containing our logos, corporate color palettes, and other design inspiration to help you understand our style.
For additional inspiration, please visit our website: www.velmora.example

Feel free to ask any questions you may have.

Best regards,

Velmora Team

```html
<!DOCTYPE html>
<html lang="en">
<head>
<meta charset="utf-8">
<title>Velmora – Insight Horizon Session template</title>
<link href="https://fonts.googleapis.com/css2?family=Poppins:wght@400;500;600;700&display=swap" rel="stylesheet">
<style>
:root{
  --stage:#109c97;
  --navy:#141a3c;
  --navy-2:#1c2352;
  --purple:#3a2a6e;
  --teal:#13a39c;
  --teal-soft:#e3f3f2;
  --magenta:#b8177a;
  --pink-soft:#f6e6ef;
  --olive:#a3a52a;
  --olive-soft:#f2f2df;
  --ink:#2b2f45;
  --muted:#6d7184;
  --paper:#ffffff;
}
*{box-sizing:border-box;margin:0;padding:0}
html,body{width:1200px;height:1125px;overflow:hidden}
body{background:var(--stage);font-family:"Poppins",sans-serif;color:var(--ink);position:relative}
.pg{position:absolute;width:159px;height:224px;background:var(--paper);overflow:hidden}
.c0{left:86px}.c1{left:260px}.c2{left:433px}.c3{left:607px}.c4{left:781px}.c5{left:955px}
.r0{top:91px}.r1{top:330px}.r2{top:570px}.r3{top:809px}
.in{position:absolute;left:16px;right:16px}
.logo{position:absolute;top:8px;right:16px;font-weight:700;font-size:6px;color:var(--navy);display:flex;align-items:center;gap:1.5px}
.logo i{width:4px;height:4px;background:var(--teal);display:block}
.foot{position:absolute;bottom:5px;left:16px;right:16px;display:flex;justify-content:space-between;font-size:1.8px;color:var(--muted)}
.h{font-weight:600;color:var(--teal);font-size:4.6px;line-height:1.2;text-transform:uppercase}
.h2{font-weight:500;color:var(--navy);font-size:4.4px;line-height:1.25}
.sub{font-weight:500;color:var(--navy);font-size:3.2px;margin-top:1px}
.p{font-size:2.2px;line-height:1.45;color:var(--muted);margin-top:2px;text-align:justify}
.p b{color:var(--ink)}
.ph{border-radius:2px}
.cols{display:grid;grid-template-columns:1fr 1fr 1fr;gap:4px}
.ch{font-size:2.9px;font-weight:600;line-height:1.2}
.mag{color:var(--magenta)}.oli{color:var(--olive)}.tea{color:var(--teal)}
.box{background:var(--teal-soft);border-radius:2px;padding:4px}
.team{border:0.5px solid #b9c4cc;border-radius:2px;padding:2.5px}
.tag{display:inline-block;background:var(--navy);color:#fff;font-size:1.7px;font-weight:600;padding:0.5px 1.5px;border-radius:0.5px}
.uc{font-size:1.7px;line-height:1.4;padding:1.2px 2px;margin-top:0.5px;color:var(--muted)}
.uc b{color:var(--ink);display:block}
.u1{background:var(--teal-soft)}.u2{background:var(--pink-soft)}.u3{background:var(--olive-soft)}
.score{border-radius:1.5px;padding:2.5px;margin-top:3px;font-size:1.8px;line-height:1.4;color:var(--muted)}
.score b{display:block;font-size:2px}
.cover{background:linear-gradient(160deg,#2d2a66 0%,var(--navy-2) 45%,var(--navy) 100%)}
.cover .clogo{position:absolute;top:16px;left:16px;color:#fff;font-weight:700;font-size:11px;display:flex;align-items:center;gap:3px}
.cover .clogo i{width:7px;height:7px;background:var(--teal);display:block}
.cover .title{position:absolute;top:56px;left:16px;color:#fff;font-weight:700;font-size:12.5px;line-height:1.05}
.cover .title span{color:var(--teal);font-size:10px;display:block}
.orb{position:absolute;left:80px;top:92px;width:68px;height:68px;border-radius:50%;background:radial-gradient(circle at 45% 45%,#e04a9a 0%,#7a2a9b 45%,#2a6fb8 80%,#1b2458 100%);border:1px solid #2fb3b0}
.meta{position:absolute;left:16px;top:122px;color:#fff;font-size:3.4px;line-height:1.45}
.meta b{font-weight:600}
.client{position:absolute;left:16px;bottom:16px;font-weight:600;font-size:9px}
table{width:100%;border-collapse:collapse;font-size:1.7px;table-layout:fixed}
th{background:var(--teal);color:#fff;text-align:left;padding:1.2px;font-weight:600}
td{padding:1.4px;border-bottom:0.4px solid #ccd3d8;color:var(--ink);white-space:nowrap;overflow:hidden}
.field{border:0.5px solid #d4d8de;border-radius:1px;padding:2px;margin-top:2px;font-size:1.7px;color:var(--muted);line-height:1.5}
.portrait{position:absolute;left:17px;top:50px;width:32px;height:32px;border-radius:50%;background:radial-gradient(circle,#c9cdd6,#8e96a8)}
.pcard{position:absolute;left:14px;top:44px;width:38px;height:80px;background:var(--teal-soft)}
.pname{position:absolute;left:14px;top:86px;width:38px;text-align:center;font-size:1.9px;font-weight:600;color:var(--teal)}
.bio{position:absolute;left:56px;right:16px;top:44px}
.bio .p{font-size:1.9px}
</style>
</head>
<body>

<!-- Row 0 -->
<section class="pg c0 r0 cover">
  <div class="clogo"><i></i>velmora</div>
  <h1 class="title">Insight Horizon<span>Session</span></h1>
  <div class="orb" role="img" aria-label="Illustration of a person facing a glowing digital interface"></div>
  <div class="meta"><b>Customer Name:</b><br>Brightwell<br><br><b>Date:</b><br>08-9-2025</div>
  <div class="client" style="color:#fff">Brightwell</div>
</section>

<section class="pg c1 r0 cover" style="background:linear-gradient(180deg,#2d2a66 0%,var(--navy-2) 55%,#6b3a7e 75%,#f3dfe8 88%,#fff 100%)">
  <div class="clogo"><i></i>velmora</div>
  <h1 class="title">Insight Horizon<span>Session</span></h1>
  <div class="orb" role="img" aria-label="Illustration of a person facing a glowing digital interface"></div>
  <div class="meta"><b>Customer Name:</b><br>Brightwell<br><br><b>Date:</b><br>08-9-2025</div>
  <div class="client" style="color:#c8102e">Brightwell</div>
</section>

<section class="pg c2 r0" style="background:var(--navy)">
  <div class="in" style="top:34px">
    <div class="h" style="font-size:4px">Table of contents</div>
    <div style="margin-top:8px;font-size:1.8px;color:#c9cde0;line-height:1">
      <div style="display:flex;justify-content:space-between;border-bottom:0.4px solid #3b4170;padding:2px 0">Executive Summary<span>01</span></div>
      <div style="display:flex;justify-content:space-between;border-bottom:0.4px solid #3b4170;padding:2px 0">Purpose of this document<span>02</span></div>
      <div style="display:flex;justify-content:space-between;border-bottom:0.4px solid #3b4170;padding:2px 0"><span><b style="color:var(--teal);font-size:3.5px">01</b> Session Overview</span><span>03</span></div>
      <div style="display:flex;justify-content:space-between;border-bottom:0.4px solid #3b4170;padding:2px 0"><span><b style="color:var(--teal);font-size:3.5px">02</b> Session Preparation</span><span>04</span></div>
      <div style="display:flex;justify-content:space-between;border-bottom:0.4px solid #3b4170;padding:2px 0"><span><b style="color:var(--teal);font-size:3.5px">03</b> Discovery Session</span><span>05</span></div>
      <div style="display:flex;justify-content:space-between;border-bottom:0.4px solid #3b4170;padding:2px 0"><span><b style="color:var(--teal);font-size:3.5px">04</b> Next steps</span><span>06</span></div>
      <div style="display:flex;justify-content:space-between;padding:2px 0">Annexes<span>07</span></div>
    </div>
  </div>
  <svg style="position:absolute;left:60px;top:140px" width="60" height="60" viewBox="0 0 60 60"><path d="M5 55 L52 8 M24 8 H52 V36" fill="none" stroke="#2a3160" stroke-width="3"/></svg>
</section>

<section class="pg c3 r0">
  <div class="logo"><i></i>velmora</div>
  <div class="in" style="top:28px">
    <div class="h">Executive summary</div>
    <p class="p">In a fast moving market, teams need a clear view of where data and automation can add real value. Many firms test new tools but struggle to turn pilots into lasting results for the business.</p>
    <p class="p">This session was run to help leaders find, rank and plan the ideas with the best return. Together we mapped needs, gaps and quick wins across the main units of the company.</p>
    <p class="p">This report sums up the key insights and clear actions from the joint session and sets a sound base for a phased plan.</p>
    <div class="h" style="margin-top:6px">Purpose of this document</div>
    <p class="p">This document gives a full record of the session and its results. It lists the use cases found, how each one was scored and the steps we propose next, so the team can act with care and confidence.</p>
    <div class="ph" role="img" aria-label="Photo of a team working together at laptops" style="margin-top:6px;height:56px;background:linear-gradient(135deg,#6d8aa0,#c9a88a 60%,#3c4c63)"></div>
  </div>
  <div class="foot"><span>Insight Horizon Session for Brightwell</span><span>03</span></div>
</section>

<section class="pg c4 r0">
  <div class="logo"><i></i>velmora</div>
  <div class="in" style="top:28px">
    <div class="h">01 Session overview:<br>&nbsp;&nbsp;&nbsp;&nbsp;The three phases of discovery</div>
    <p class="p">The session is built to guide teams through the full path from idea to plan. Each phase has a clear aim and a set of simple tools.</p>
    <div class="sub" style="margin-top:4px">Our Approach: The Three Phases of Discovery</div>
    <div class="cols" style="margin-top:3px">
      <div><div class="ch mag">Inspire: Igniting Possibilities</div><p class="p" style="font-size:1.8px">We open with real cases and simple demos so every person sees what is possible and shares ideas freely with the group.</p></div>
      <div><div class="ch mag">Discover: Unearthing Core Opportunities</div><p class="p" style="font-size:1.8px">Small groups work on real pain points and turn them into clear use cases with a named owner and goal.</p></div>
      <div><div class="ch mag">Prioritize: Defining Your Strategic Roadmap</div><p class="p" style="font-size:1.8px">Each case is scored on impact and effort so the team can agree on a short list and a first plan.</p></div>
    </div>
    <div class="box" style="margin-top:5px;height:34px;display:flex;align-items:center;justify-content:center;gap:4px;font-size:1.7px;color:#fff;font-weight:600;text-align:center">
      <div style="width:18px;height:18px;border-radius:50%;background:var(--teal);display:flex;align-items:center;justify-content:center;border:1px solid var(--olive)">Inspire</div><span style="color:var(--navy)">→</span>
      <div style="width:18px;height:18px;border-radius:50%;background:var(--magenta);display:flex;align-items:center;justify-content:center">Discover</div><span style="color:var(--navy)">→</span>
      <div style="width:18px;height:18px;border-radius:50%;background:var(--olive);display:flex;align-items:center;justify-content:center">Prioritize</div>
    </div>
  </div>
  <div class="foot"><span>Insight Horizon Session for Brightwell</span><span>04</span></div>
</section>

<section class="pg c5 r0">
  <div class="logo"><i></i>velmora</div>
  <div class="in" style="top:28px">
    <div class="h">02 Session preparation</div>
    <p class="p">To get the most from the day we prepared with care, shaping every part of the agenda around the needs of the client team.</p>
    <div class="cols" style="margin-top:8px">
      <div><div class="ch mag">A Foundation of Diverse Expertise</div><p class="p" style="font-size:1.8px">We asked the client to invite people from many areas so that the ideas came from every corner of the business and the group had a full view of the work.</p></div>
      <div><div class="ch mag">Leveraging Participant Insights</div><p class="p" style="font-size:1.8px">Before the day each person filled in a short survey. Their answers told us which goals, tools and gaps mattered most to them.</p></div>
      <div><div class="ch mag">Customizing Your Session Experience</div><p class="p" style="font-size:1.8px">With these insights we tuned the talks, examples and tasks so that each part spoke to the real world of the team in the room.</p></div>
    </div>
    <div class="box" style="margin-top:10px;text-align:center;font-size:2.6px;font-weight:500;color:var(--navy);line-height:1.4;padding:5px">
      <span class="tea" style="font-size:5px;font-weight:700">“</span> Our goal is to create an environment where every participant <span class="mag">feels empowered</span> to contribute, resulting in a more <span class="oli">collaborative</span> and <span class="tea">effective outcome</span> for your organization. <span class="tea" style="font-size:5px;font-weight:700">”</span>
    </div>
  </div>
  <div class="foot"><span>Insight Horizon Session for Brightwell</span><span>05</span></div>
</section>

<!-- Row 1 -->
<section class="pg c0 r1">
  <div class="logo"><i></i>velmora</div>
  <div class="in" style="top:28px">
    <div class="h">03 Discovery session</div>
    <p class="p">This part gives the details of the session run with the client team to begin their journey.</p>
    <div class="box" style="margin-top:4px;font-size:1.8px;line-height:1.6;color:var(--muted)">
      <b style="color:var(--ink)">Customer:</b> Brightwell<br><b style="color:var(--ink)">Date:</b> Session date and time<br><b style="color:var(--ink)">Location:</b> Session venue, head office<br><b style="color:var(--ink)">Velmora Leaders:</b> The session was run by our expert team, who guided the talks and tasks.<br>(1) Leader Name one<br>(2) Leader Name two<br><i style="color:var(--ink)">The full profile of each leader is in Annex 3.</i>
    </div>
    <div class="h2" style="margin-top:5px">Discovery Session Phase I: Inspire</div>
    <p class="p">As noted before, this phase set the scene. We shared real examples and short demos, chosen to fit the sector, so the group could see what is possible and begin to think big.</p>
    <p class="p">The cases were linked to the answers from the survey so every person saw value close to their own work.</p>
    <div class="h2" style="margin-top:4px">Discovery Session Phase II: Discover</div>
    <p class="p">In this phase teams worked in small groups. Each group looked at its daily tasks and named the points where time, cost or quality could be improved.</p>
  </div>
  <div class="foot"><span>Insight Horizon Session for Brightwell</span><span>06</span></div>
</section>

<section class="pg c1 r1">
  <div class="logo"><i></i>velmora</div>
  <div class="in" style="top:28px">
    <p class="p">The leaders helped the teams stay open and creative, and gave each group a few guide questions to start.</p>
    <div class="box" style="margin-top:3px;font-size:1.8px;line-height:1.7;color:var(--ink);padding-left:8px">• What business outcome do you want to improve?<br>• Are your tools and processes holding you back?<br>• Are you using your data to manage your business?<br>• Have you felt the need for smarter tools?</div>
    <p class="p">Each team then set out the use cases it found most useful:</p>
    <div class="team" style="margin-top:2px"><span class="tag">TEAM 1</span>
      <div class="uc u1"><b>Employee assistant</b>A chatbot that answers staff questions on leave or expense policy.</div>
      <div class="uc u2"><b>Customer support assistant</b>A chatbot that answers product questions and order status.</div>
      <div class="uc u3"><b>Medical appointment reminder</b>A voice agent that calls patients ahead to confirm or change visits.</div>
    </div>
    <div class="team" style="margin-top:3px"><span class="tag">TEAM 2</span>
      <div class="uc u1"><b>Employee assistant</b>A chatbot that answers staff questions on leave or expense policy.</div>
      <div class="uc u2"><b>Customer support assistant</b>A chatbot that answers product questions and order status.</div>
      <div class="uc u3"><b>Medical appointment reminder</b>A voice agent that calls patients ahead to confirm or change visits.</div>
    </div>
  </div>
  <div class="foot"><span>Insight Horizon Session for Brightwell</span><span>07</span></div>
</section>

<section class="pg c2 r1">
  <div class="logo"><i></i>velmora</div>
  <div class="in" style="top:26px">
    <div class="team"><span class="tag">TEAM 1</span>
      <div class="uc u1"><b>Employee assistant</b>A chatbot that answers staff questions on leave or expense policy.</div>
      <div class="uc u2"><b>Customer support assistant</b>A chatbot that answers product questions and order status.</div>
      <div class="uc u3"><b>Medical appointment reminder</b>A voice agent that calls patients ahead to confirm or change visits.</div>
    </div>
    <div class="team" style="margin-top:3px"><span class="tag">TEAM 2</span>
      <div class="uc u1"><b>Employee assistant</b>A chatbot that answers staff questions on leave or expense policy.</div>
      <div class="uc u2"><b>Customer support assistant</b>A chatbot that answers product questions and order status.</div>
      <div class="uc u3"><b>Medical appointment reminder</b>A voice agent that calls patients ahead to confirm or change visits.</div>
    </div>
    <div class="team" style="margin-top:3px"><span class="tag">TEAM 3</span>
      <div class="uc u1"><b>Employee assistant</b>A chatbot that answers staff questions on leave or expense policy.</div>
      <div class="uc u2"><b>Customer support assistant</b>A chatbot that answers product questions and order status.</div>
      <div class="uc u3"><b>Medical appointment reminder</b>A voice agent that calls patients ahead to confirm or change visits.</div>
    </div>
  </div>
  <div class="foot"><span>Insight Horizon Session for Brightwell</span><span>08</span></div>
</section>

<section class="pg c3 r1">
  <div class="logo"><i></i>velmora</div>
  <div class="in" style="top:28px">
    <div class="h2">Discovery Session Phase III: Prioritize</div>
    <p class="p">The last phase turned the list into a plan. Each use case was placed on a simple matrix by its impact and its feasibility, giving a clear view of where to begin.</p>
    <div class="box" style="margin-top:3px;height:76px;position:relative">
      <svg width="119" height="68" viewBox="0 0 119 68" style="position:absolute;left:4px;top:4px">
        <rect x="14" y="2" width="102" height="56" fill="#fff"/>
        <line x1="65" y1="6" x2="65" y2="54" stroke="#1c2352" stroke-width="0.5"/>
        <line x1="18" y1="30" x2="112" y2="30" stroke="#1c2352" stroke-width="0.5"/>
        <text x="2" y="6" font-size="3" font-family="Poppins" fill="#1c2352" font-weight="600">High</text>
        <text x="2" y="57" font-size="3" font-family="Poppins" fill="#1c2352" font-weight="600">Low</text>
        <text x="8" y="36" font-size="3.2" font-family="Poppins" fill="#1c2352" font-weight="600" transform="rotate(-90 8 36)">Impact</text>
        <text x="20" y="64" font-size="3" font-family="Poppins" fill="#1c2352" font-weight="600">Low</text>
        <text x="52" y="65" font-size="4" font-family="Poppins" fill="#1c2352" font-weight="600">Feasibility</text>
        <text x="104" y="64" font-size="3" font-family="Poppins" fill="#1c2352" font-weight="600">High</text>
        <circle cx="100" cy="10" r="5" fill="none" stroke="#a3a52a" stroke-width="0.6" stroke-dasharray="1 1"/>
        <g fill="#b8177a"><circle cx="50" cy="14" r="1.3"/><circle cx="90" cy="22" r="1.3"/><circle cx="46" cy="36" r="1.3"/><circle cx="102" cy="18" r="1.3"/><circle cx="88" cy="50" r="1.3"/></g>
        <g fill="#a3a52a"><circle cx="22" cy="12" r="1.3"/><circle cx="30" cy="40" r="1.3"/><circle cx="80" cy="34" r="1.3"/><circle cx="100" cy="10" r="1.3"/></g>
        <g fill="#13a39c"><circle cx="60" cy="22" r="1.3"/><circle cx="38" cy="52" r="1.3"/><circle cx="74" cy="26" r="1.3"/><circle cx="95" cy="12" r="1.3"/></g>
      </svg>
    </div>
    <div class="ch mag" style="margin-top:5px">Impact</div>
    <p class="p">Impact was scored on four points so the full scope of value was seen.</p>
    <p class="p">• <b>Financial Outcome:</b> the effect on revenue, cost and margin.<br>• <b>Operational Efficiency:</b> time saved, fewer errors and faster work.<br>• <b>Strategic Alignment:</b> fit with the goals of the company.<br>• <b>Customer Experience:</b> better service and more loyal clients.</p>
  </div>
  <div class="foot"><span>Insight Horizon Session for Brightwell</span><span>09</span></div>
</section>

<section class="pg c4 r1">
  <div class="logo"><i></i>velmora</div>
  <div class="in" style="top:28px">
    <div class="ch mag">Feasibility:</div>
    <p class="p">Feasibility was scored on three factors to spot likely blocks early.</p>
    <p class="p">• <b>Process Complexity:</b> how many steps, rules and hand-offs the process has, and how often it changes.<br>• <b>Integrations:</b> the effort to link the solution with current systems and tools.<br>• <b>Data Availability:</b> whether the right data exists, in the right format, at the right time.</p>
    <p class="p">As a result of this work, the group agreed a short list of priority use cases, each with a clear owner and a first set of steps toward delivery.</p>
    <div class="ph" role="img" aria-label="Photo of two engineers reviewing a tablet in a server room" style="margin-top:30px;height:60px;background:linear-gradient(135deg,#1d3f6e,#3f7fb0 55%,#0f2343)"></div>
  </div>
  <div class="foot"><span>Insight Horizon Session for Brightwell</span><span>10</span></div>
</section>

<section class="pg c5 r1">
  <div class="logo"><i></i>velmora</div>
  <div class="in" style="top:28px">
    <div class="h2">Prioritized Use Case 1</div>
    <div class="sub">Medical appointment reminder</div>
    <p class="p">A voice agent that calls patients ahead of time to confirm, move or cancel their visits.</p>
    <p class="p">This agent cuts no-shows and keeps the clinic diary full by reaching patients days before each visit.</p>
    <div class="ch mag" style="margin-top:3px">How it Works:</div>
    <p class="p">• <b>Appointment Retrieval:</b> the agent reads the cloud database to fetch next visits.<br>• <b>Automated Patient Outreach:</b> it calls each patient with the key details.<br>• <b>Interactive Options:</b> the patient picks an action.<br>&nbsp;&nbsp;– <b>Confirm:</b> the visit is kept.<br>&nbsp;&nbsp;– <b>Cancel:</b> the slot is freed.<br>&nbsp;&nbsp;– <b>Reschedule:</b> new times are offered.</p>
    <p class="p">The clinic diary stays current and patients get timely reminders.</p>
    <div class="score u2"><b class="mag">Impact: High</b>Missed visits cost the clinic money and time. Fewer no-shows lift revenue and use of staff.</div>
    <div class="score u3"><b class="oli">Feasibility: High</b>Data and calling tools are in place, so the agent can be deployed with little effort.</div>
  </div>
  <div class="foot"><span>Insight Horizon Session for Brightwell</span><span>11</span></div>
</section>

<!-- Row 2 -->
<section class="pg c0 r2">
  <div class="logo"><i></i>velmora</div>
  <div class="in" style="top:28px">
    <div class="h2">Prioritized Use Case 2</div>
    <div class="sub">Medical appointment reminder</div>
    <p class="p">A voice agent that calls patients ahead of time to confirm, move or cancel their visits.</p>
    <p class="p">This agent cuts no-shows and keeps the clinic diary full by reaching patients days before each visit.</p>
    <div class="ch mag" style="margin-top:3px">How it Works:</div>
    <p class="p">• <b>Appointment Retrieval:</b> the agent reads the cloud database to fetch next visits.<br>• <b>Automated Patient Outreach:</b> it calls each patient with the key details.<br>• <b>Interactive Options:</b> the patient picks an action.<br>&nbsp;&nbsp;– <b>Confirm:</b> the visit is kept.<br>&nbsp;&nbsp;– <b>Cancel:</b> the slot is freed.<br>&nbsp;&nbsp;– <b>Reschedule:</b> new times are offered.</p>
    <p class="p">The clinic diary stays current and patients get timely reminders.</p>
    <div class="score u2"><b class="mag">Impact: High</b>Missed visits cost the clinic money and time. Fewer no-shows lift revenue and use of staff.</div>
    <div class="score u3"><b class="oli">Feasibility: High</b>Data and calling tools are in place, so the agent can be deployed with little effort.</div>
  </div>
  <div class="foot"><span>Insight Horizon Session for Brightwell</span><span>12</span></div>
</section>

<section class="pg c1 r2">
  <div class="logo"><i></i>velmora</div>
  <div class="in" style="top:28px">
    <div class="h2">Prioritized Use Case 3</div>
    <div class="sub">Medical appointment reminder</div>
    <p class="p">A voice agent that calls patients ahead of time to confirm, move or cancel their visits.</p>
    <p class="p">This agent cuts no-shows and keeps the clinic diary full by reaching patients days before each visit.</p>
    <div class="ch mag" style="margin-top:3px">How it Works:</div>
    <p class="p">• <b>Appointment Retrieval:</b> the agent reads the cloud database to fetch next visits.<br>• <b>Automated Patient Outreach:</b> it calls each patient with the key details.<br>• <b>Interactive Options:</b> the patient picks an action.<br>&nbsp;&nbsp;– <b>Confirm:</b> the visit is kept.<br>&nbsp;&nbsp;– <b>Cancel:</b> the slot is freed.<br>&nbsp;&nbsp;– <b>Reschedule:</b> new times are offered.</p>
    <div class="score u2"><b class="mag">Impact: High</b>Missed visits cost the clinic money and time. Fewer no-shows lift revenue and use of staff.</div>
    <div class="score u3"><b class="oli">Feasibility: High</b>Data and calling tools are in place, so the agent can be deployed with little effort.</div>
    <p class="p">The session was a clear success, with strong energy from every team and a solid list of ideas ready for the next stage.</p>
  </div>
  <div class="foot"><span>Insight Horizon Session for Brightwell</span><span>13</span></div>
</section>

<section class="pg c2 r2">
  <div class="logo"><i></i>velmora</div>
  <div class="in" style="top:28px">
    <div class="h">04 Next steps</div>
    <p class="p">Building on the ideas and clarity gained in the session, the next phase turns the chosen use cases into real results. We propose a clear plan that moves from design to a first working release.</p>
    <svg width="127" height="50" viewBox="0 0 127 50" style="margin-top:4px">
      <circle cx="12" cy="25" r="9" fill="#1c2352"/><text x="12" y="24" font-size="2.6" fill="#fff" text-anchor="middle" font-family="Poppins" font-weight="600">Use</text><text x="12" y="27.5" font-size="2.6" fill="#fff" text-anchor="middle" font-family="Poppins" font-weight="600">Case</text>
      <path d="M24 25 h8" stroke="#1c2352" stroke-width="0.6"/>
      <rect x="34" y="12" width="30" height="8" fill="#13a39c"/><text x="49" y="17" font-size="2" fill="#fff" text-anchor="middle" font-family="Poppins">Functional req.</text>
      <rect x="34" y="30" width="30" height="8" fill="#13a39c"/><text x="49" y="35" font-size="2" fill="#fff" text-anchor="middle" font-family="Poppins">IT assets</text>
      <path d="M66 25 h6" stroke="#1c2352" stroke-width="0.6"/>
      <g fill="none" stroke="#13a39c" stroke-width="0.8"><circle cx="80" cy="10" r="5"/><circle cx="80" cy="25" r="5"/><circle cx="80" cy="40" r="5"/></g>
      <g font-size="2.2" fill="#1c2352" font-family="Poppins" font-weight="600"><text x="88" y="11">Architecture</text><text x="88" y="26">Implementation plan</text><text x="88" y="41">Governance</text></g>
    </svg>
    <p class="p">To deliver this, we propose a joint effort between our team and yours, focused on the following key steps:</p>
    <p class="p">• <b>Detailed Functional Requirements:</b> we will work with the business to define each use case in depth, including the flows, rules, users and success measures that guide the build.</p>
    <p class="p">• <b>IT Asset Assessment:</b> we will review the current systems, data and tools to see what can be reused and where new parts are needed, so the design is sound and cost effective.</p>
    <p class="p">We will also review the current platform to confirm it can support the new work at scale.</p>
  </div>
  <div class="foot"><span>Insight Horizon Session for Brightwell</span><span>14</span></div>
</section>

<section class="pg c3 r2">
  <div class="logo"><i></i>velmora</div>
  <div class="in" style="top:26px">
    <p class="p">Internal documents on rules, processes and policies will be reviewed. We will also check the need to bring in outside data sources and how they will be kept current.</p>
    <p class="p">• <b>Human Capital Assessment:</b> we will review the skills in house to build and run the new solutions, and plan any training needed to close gaps.</p>
    <p class="p">The result of this joint work will be a full view of what is needed, a clear design and a phased plan with time, cost and a model to govern the work across its life.</p>
    <div class="ph" role="img" aria-label="Photo of a person in a data centre surrounded by glowing data streams" style="margin-top:40px;height:60px;background:linear-gradient(135deg,#0c2a44,#2a7da0 55%,#0b1d33)"></div>
  </div>
  <div class="foot"><span>Insight Horizon Session for Brightwell</span><span>15</span></div>
</section>

<section class="pg c4 r2">
  <div class="logo"><i></i>velmora</div>
  <div class="in" style="top:150px">
    <div class="h2">About Velmora</div>
    <p class="p">We are a firm of experts in the design and delivery of solutions in cloud, data and smart automation.</p>
    <p class="p">Our aim is to help our clients grow by putting data at the heart of every decision. We build lasting partnerships and create value through skill, care and a clear focus on results.</p>
    <p class="p">More information in <b>www.velmora.example</b></p>
  </div>
  <div class="foot"><span>Insight Horizon Session for Brightwell</span><span>16</span></div>
</section>

<section class="pg c5 r2">
  <div class="logo"><i></i>velmora</div>
  <div class="in" style="top:28px">
    <div class="h">Annex 1</div>
    <div class="sub" style="font-size:4px">List of Participants</div>
    <table style="margin-top:5px">
      <colgroup><col style="width:17%"><col style="width:11%"><col style="width:16%"><col style="width:20%"><col style="width:22%"><col style="width:14%"></colgroup>
      <tr><th># Part.</th><th>Name</th><th>Surname</th><th>Company Role</th><th>Email</th><th>Telephone</th></tr>
      <tr><td>1</td><td>xxx</td><td>Thessaly</td><td>Controller</td><td>xxx@mail.ex</td><td>xxx</td></tr>
      <tr><td>2</td><td>xxx</td><td>Dorvane</td><td>CEO</td><td>xxx@mail.ex</td><td>xxx</td></tr>
      <tr><td>3</td><td>xxx</td><td>Marlowe</td><td>COO</td><td>xxx@mail.ex</td><td>xxx</td></tr>
      <tr><td>4</td><td>xxx</td><td>Kessling</td><td>IT Manager</td><td>xxx@mail.ex</td><td>xxx</td></tr>
      <tr><td>5</td><td>xxx</td><td>Pendry</td><td>Marketing</td><td>xxx@mail.ex</td><td>xxx</td></tr>
      <tr><td>6</td><td>xxx</td><td>Quillon</td><td>Copy &amp; Content</td><td>xxx@mail.ex</td><td>xxx</td></tr>
    </table>
  </div>
  <div class="foot"><span>Insight Horizon Session for Brightwell</span><span>17</span></div>
</section>

<!-- Row 3 -->
<section class="pg c0 r3">
  <div class="logo"><i></i>velmora</div>
  <div class="in" style="top:28px">
    <div class="h">Annex 2</div>
    <div class="sub" style="font-size:4px">Preparatory survey</div>
    <div style="margin-top:4px;border:0.5px solid #d4d8de;border-top:2px solid #5b3aa8;padding:3px;border-radius:1px">
      <div style="font-size:3px;color:var(--ink)">Insight Horizon Session – Pre Survey</div>
      <div style="font-size:1.6px;color:var(--muted);line-height:1.5;margin-top:2px">Please answer these questions before the session so we can tailor it to your team. It takes about five minutes.</div>
    </div>
    <div class="field">How familiar are you with smart automation?<br>○ Not at all &nbsp;○ A little &nbsp;○ Quite &nbsp;○ Very</div>
    <div class="field">Have you used any automation tool at work?<br>Long answer text</div>
    <div class="field">Which process in your area could be improved?<br>Long answer text</div>
    <div class="field">What are the main goals of your area this year?<br>Long answer text</div>
    <div class="field">What do you expect from the session?<br>Long answer text</div>
  </div>
  <div class="foot"><span>Insight Horizon Session for Brightwell</span><span>18</span></div>
</section>

<section class="pg c1 r3">
  <div class="logo"><i></i>velmora</div>
  <div class="in" style="top:28px">
    <div class="h">Annex 3.1</div>
    <div class="sub" style="font-size:3.6px">Velmora Business Leader - Tomas Arlen</div>
  </div>
  <div class="pcard"></div>
  <div class="portrait" role="img" aria-label="Portrait photo of Tomas Arlen"></div>
  <div class="pname">Tomas Arlen</div>
  <div class="bio">
    <p class="p">Tomas Arlen is a seasoned leader in tech with a long record in business growth and building strong teams across many markets.</p>
    <p class="p">Before joining Velmora he led cloud sales at a large software group, where he grew the partner base and opened new regions.</p>
    <p class="p">He has worked with clients in retail, health and finance, helping them shape plans for data and automation that deliver clear value.</p>
    <p class="p">He holds a degree in telecom engineering and a master in business administration.</p>
  </div>
  <div class="foot"><span>Insight Horizon Session for Brightwell</span><span>19</span></div>
</section>

<section class="pg c2 r3">
  <div class="logo"><i></i>velmora</div>
  <div class="in" style="top:28px">
    <div class="h">Annex 3.2</div>
    <div class="sub" style="font-size:3.6px">Velmora Business Leader - Marc Oriol</div>
  </div>
  <div class="pcard"></div>
  <div class="portrait" role="img" aria-label="Portrait photo of Marc Oriol"></div>
  <div class="pname">Marc Oriol</div>
  <div class="bio">
    <p class="p">Marc Oriol is a known leader in data and analytics with a strong record of growth and of building high performing teams.</p>
    <p class="p">Before Velmora he held senior roles at global software firms, leading cloud and data teams across several regions.</p>
    <p class="p">His work covers data platforms, analytics and smart services, and he has helped many firms turn data into better decisions.</p>
    <p class="p">He holds a degree in telecom engineering and a master in business.</p>
  </div>
  <div class="foot"><span>Insight Horizon Session for Brightwell</span><span>20</span></div>
</section>

<section class="pg c3 r3">
  <div class="logo"><i></i>velmora</div>
  <div class="in" style="top:28px">
    <div class="h">Annex 3.3</div>
    <div class="sub" style="font-size:3.6px">Velmora Business Leader - Dario Lenz</div>
  </div>
  <div class="pcard"></div>
  <div class="portrait" role="img" aria-label="Portrait photo of Dario Lenz"></div>
  <div class="pname">Dario Lenz</div>
  <div class="bio">
    <p class="p">Dario Lenz is a tech leader with a long record in shaping and running major IT services such as cloud, data and apps.</p>
    <p class="p">Before Velmora he led large delivery teams and managed key accounts for global clients in many sectors.</p>
    <p class="p">He has also served as chief tech officer, leading change and new platforms across the business.</p>
    <p class="p">He holds a degree in computer engineering and a master in business.</p>
  </div>
  <div class="foot"><span>Insight Horizon Session for Brightwell</span><span>21</span></div>
</section>

<section class="pg c4 r3" style="background:linear-gradient(180deg,var(--navy-2) 0%,var(--navy) 50%,#0b1130 100%)">
  <div style="position:absolute;left:0;right:0;top:102px;display:flex;justify-content:center;align-items:center;gap:3px;color:#fff;font-weight:700;font-size:14px"><i style="width:9px;height:9px;background:var(--teal);display:block"></i>velmora</div>
  <div style="position:absolute;left:0;right:0;bottom:14px;text-align:center;color:#c9cde0;font-size:1.9px">www.velmora.example</div>
</section>

</body>
</html>
```